WordPress Site Clean up

We are a small wireless networking company in Norther Colorado. We have a basic layout to our new website, and require a person or persons who can clean the new site up so we can go live with it in the coming weeks. Our company has the logo and content, we just need to clean the formatting up, improve the colors/graphics. It is currently a PLUMVERSA. We also need help making our project pictures look better on the website, and clean up the images all around.

The website can be found at: www.5xpfieldgrid.com/newsite

We can provide you with photos and more content, but we have gone as far as we can with "building" the wordpress site.

```html
<!DOCTYPE html>
<html lang="en">
<head>
<meta charset="utf-8">
<title>Fieldgrid Networks</title>
<link rel="stylesheet" href="https://fonts.googleapis.com/css2?family=Roboto:wght@400;500;700&display=swap">
<style>
:root{
  --green:#7cbf34;
  --green-dark:#5e9c1d;
  --green-line:#8fce4c;
  --ink:#333;
  --band:#343434;
  --footer:#1f1f1f;
  --panel:#f0f0f0;
  --white:#fff;
}
*{box-sizing:border-box;margin:0;padding:0}
html,body{width:721px;height:1200px;overflow:hidden;background:var(--white);font-family:'Roboto',Arial,sans-serif;color:var(--ink)}
.page{position:relative;width:721px;height:1200px}
.header{position:absolute;left:0;top:0;width:721px;height:78px;background:var(--green)}
.brand{position:absolute;left:52px;top:30px;display:flex;align-items:center;gap:6px;color:var(--white);font-size:21px;font-weight:500;letter-spacing:-.5px}
.brand-dot{width:12px;height:12px;background:var(--white);border-radius:50%}
.phone{position:absolute;right:53px;top:17px;color:var(--white);font-size:10.5px}
.nav{position:absolute;right:53px;top:42px;display:flex;gap:33px}
.nav a{color:var(--white);text-decoration:none;font-size:9.5px}
.hero{position:absolute;left:0;top:78px;width:721px;height:357px;background:linear-gradient(180deg,#9fb8dd 0%,#c7d4e6 42%,#5b6f93 62%,#26396a 85%,#1e3060 100%)}
.hero-copy{position:absolute;left:54px;top:66px;color:var(--white)}
.hero-title{font-size:22px;font-weight:700;text-transform:uppercase;letter-spacing:-.3px;text-shadow:0 1px 2px rgba(0,0,0,.4)}
.hero-title span{color:#2a2a2a}
.hero-sub{font-size:15px;margin-top:10px}
.hero-line{font-size:14px;margin-top:9px}
.btn-dark{display:inline-block;margin-top:19px;background:#222;color:var(--white);font-size:11.5px;font-weight:500;padding:9px 12px;border-radius:4px}
.dots{position:absolute;left:54px;top:256px;display:flex;gap:5px}
.dots i{display:block;width:20px;height:2px;background:var(--white)}
.dots i.on{background:var(--green)}
.features{position:absolute;left:53px;top:355px;width:616px;height:169px;display:flex;box-shadow:0 8px 12px -6px rgba(0,0,0,.35)}
.feature{width:154px;height:169px;text-align:center;color:var(--white);padding-top:22px}
.feature:nth-child(odd){background:var(--green-dark)}
.feature:nth-child(even){background:var(--green)}
.feature svg{width:36px;height:36px}
.feature h3{font-size:10.5px;font-weight:500;margin-top:10px}
.feature p{font-size:7px;line-height:10.5px;margin:6px 14px 0;color:var(--white)}
.btn-light{display:inline-block;margin-top:10px;width:64px;height:17px;line-height:17px;background:linear-gradient(#fafafa,#d8d8d8);color:#333;font-size:6.5px;border-radius:2px;box-shadow:0 1px 2px rgba(0,0,0,.4)}
.photo-frame{position:absolute;left:53px;top:550px;width:187px;height:188px;background:var(--white);padding:3px;box-shadow:0 1px 4px rgba(0,0,0,.4)}
.photo{width:100%;height:100%;background:linear-gradient(135deg,#e8e6e2,#9b9893 55%,#3a3a3a)}
.tabs{position:absolute;left:250px;top:552px;width:416px;height:183px;background:var(--panel);box-shadow:0 1px 3px rgba(0,0,0,.3)}
.tab-bar{display:flex;height:28px;background:var(--green)}
.tab{color:var(--white);font-size:7px;text-transform:uppercase;line-height:28px;text-align:center;border-right:1px solid var(--green-line);position:relative}
.tab:last-child{border-right:0}
.tab.active{background:var(--green-dark)}
.tab.active:after{content:"";position:absolute;left:36px;bottom:-5px;border:5px solid transparent;border-bottom:0;border-top-color:var(--green-dark)}
.tab-body{padding:17px 15px 0 15px;font-size:8.5px;line-height:15.8px;color:#444}
.btn-green{display:inline-block;margin-top:8px;background:var(--green-dark);color:var(--white);font-size:6.5px;line-height:6.5px;padding:5px 13px;border-radius:2px;box-shadow:0 1px 2px rgba(0,0,0,.35)}
.projects{position:absolute;left:0;top:758px;width:721px;height:223px;background:var(--band);text-align:center;color:var(--white)}
.projects h2,.partners h2{font-size:12.5px;font-weight:500;padding-top:25px}
.projects p{font-size:8.5px;margin-top:8px}
.cards{position:absolute;left:89px;top:78px;display:flex;gap:11px}
.card{width:123px;height:119px;background:var(--white);color:#222}
.card-img{height:88px}
.card strong{display:block;font-size:7px;font-weight:400;margin-top:7px}
.card small{display:block;font-size:6px;margin-top:2px}
.partners{position:absolute;left:0;top:981px;width:721px;height:132px;text-align:center;color:#222}
.partners h2{padding-top:23px}
.partner-row{position:absolute;left:63px;top:71px;width:600px;display:flex;justify-content:space-between;align-items:center}
.partner{display:flex;align-items:center;gap:5px;font-size:11px;font-weight:700;color:#2a2a2a}
.partner i{width:12px;height:12px;background:#1d4e9a;display:block}
.footer{position:absolute;left:0;top:1113px;width:721px;height:87px;background:var(--footer);color:var(--white)}
.footer-links{position:absolute;left:52px;top:28px;font-size:8.5px}
.copyright{position:absolute;left:52px;top:46px;font-size:8.5px}
.follow{position:absolute;left:546px;top:23px;font-size:8.5px}
.social{position:absolute;left:547px;top:41px;display:flex;gap:2px}
.social i{display:block;width:18px;height:18px}
</style>
</head>
<body>
<div class="page">
  <header class="header">
    <div class="brand"><span class="brand-dot"></span>Fieldgrid Networks</div>
    <div class="phone">Call Us Today &nbsp;1-800-555-0142</div>
    <nav class="nav"><a href="#">Fieldgrid About Us</a><a href="#">Fieldgrid Contact Us</a><a href="#">Fieldgrid Blog</a></nav>
  </header>

  <section class="hero" role="img" aria-label="Radio and telecom towers on a hilltop above a city and sea under a blue sky">
    <div class="hero-copy">
      <div class="hero-title">Welcome to Fieldgrid <span>Networks</span></div>
      <div class="hero-sub">All Your Wireless Needs A Professional Solution</div>
      <div class="hero-line">Lorem Ipsum is simply dummy text of the printing</div>
      <span class="btn-dark">CLICK HERE</span>
    </div>
    <div class="dots"><i></i><i class="on"></i><i></i><i></i></div>
  </section>

  <section class="features">
    <div class="feature">
      <svg viewBox="0 0 36 36" fill="none" stroke="#fff" stroke-width="2.4"><rect x="7" y="7" width="22" height="16" rx="1"/><path d="M3 27h30l-2 3H5z" fill="#fff"/></svg>
      <h3>SERVICES</h3>
      <p>Lorem Ipsum has been the industry's standard dummy text ever since the 1500s, when an unknown printer</p>
      <span class="btn-light">READ MORE</span>
    </div>
    <div class="feature">
      <svg viewBox="0 0 36 36" fill="#fff"><circle cx="14" cy="20" r="9"/><circle cx="14" cy="20" r="3.5" fill="#7cbf34"/><circle cx="27" cy="10" r="6"/><circle cx="27" cy="10" r="2.2" fill="#7cbf34"/><circle cx="27" cy="28" r="5"/><circle cx="27" cy="28" r="1.8" fill="#7cbf34"/></svg>
      <h3>SOLUTIONS</h3>
      <p>Lorem Ipsum has been the industry's standard dummy text ever since the 1500s, when an unknown printer</p>
      <span class="btn-light">READ MORE</span>
    </div>
    <div class="feature">
      <svg viewBox="0 0 36 36" fill="#fff"><path d="M33 3L3 17l10 3 3 12 5-8 8 4z"/></svg>
      <h3>DESIGN</h3>
      <p>Lorem Ipsum has been the industry's standard dummy text ever since the 1500s, when an unknown printer</p>
      <span class="btn-light">READ MORE</span>
    </div>
    <div class="feature">
      <svg viewBox="0 0 36 36" fill="#fff"><circle cx="18" cy="10" r="5.5"/><circle cx="8" cy="13" r="4"/><circle cx="28" cy="13" r="4"/><path d="M9 32c0-9 4-14 9-14s9 5 9 14z"/><path d="M1 30c0-7 3-11 7-11 2 0 3 1 4 2-2 3-3 6-3 9z"/><path d="M35 30c0-7-3-11-7-11-2 0-3 1-4 2 2 3 3 6 3 9z"/></svg>
      <h3>WHAT WE DO</h3>
      <p>Lorem Ipsum has been the industry's standard dummy text ever since the 1500s, when an unknown printer</p>
      <span class="btn-light">READ MORE</span>
    </div>
  </section>

  <div class="photo-frame"><div class="photo" role="img" aria-label="Network equipment rack mounted in a server room"></div></div>

  <section class="tabs">
    <div class="tab-bar">
      <span class="tab active" style="width:79px">Our Solutions</span><span class="tab" style="width:91px">Customer Focus</span><span class="tab" style="width:79px">Safety First</span><span class="tab" style="width:94px">Professionalism</span><span class="tab" style="width:73px">Quality</span>
    </div>
    <div class="tab-body">
      Lorem Ipsum has been the industry's standard dummy text ever since the 1500s, when an unknown printer took a galley of type and scrambled it to make a type specimen book. It has survived not only five centuries, but also the leap into electronic typesetting, remaining essentially unchanged. It was popularised in the 1960s with the release of Veltrane sheets containing Lorem Ipsum passages, and more recently with desktop publishing software like Foliowright Layout including versions of Lorem Ipsum Lorem Ipsum has been the industry's standard dummy text ever since the 1500s,
      <br><span class="btn-green">READ MORE</span>
    </div>
  </section>

  <section class="projects">
    <h2>OUR LATEST PROJECTS</h2>
    <p>Take a look at our latest projects and learn more about what we can do for you and your networking needs.</p>
    <div class="cards">
      <div class="card"><div class="card-img" role="img" aria-label="Point-to-point dish antenna on a pole" style="background:linear-gradient(160deg,#b7b4ae,#7a736a 60%,#4d4740)"></div><strong>Kestrel Air Q16 1.6 Gbps</strong><small>Point-to-Point</small></div>
      <div class="card"><div class="card-img" role="img" aria-label="Wireless antenna at a lumber yard" style="background:linear-gradient(180deg,#c9ccd0,#9ea2a6 55%,#6c6e6b)"></div><strong>Wireless Solution Lumber Yard</strong><small>Indoor-Wireless</small></div>
      <div class="card"><div class="card-img" role="img" aria-label="Radio unit mounted on a rooftop mast" style="background:linear-gradient(180deg,#d4d8dd,#9a9d9c 55%,#6f6a60)"></div><strong>Linkspan LX80</strong><small>Point-to-Point</small></div>
      <div class="card"><div class="card-img" role="img" aria-label="Dual radio links on a rooftop" style="background:linear-gradient(180deg,#8aa0c2,#b6b8b6 55%,#8a7f70)"></div><strong>Dual Linkspan LX80 Links</strong><small>Point-to-Point</small></div>
    </div>
  </section>

  <section class="partners">
    <h2>OUR PARTNERS</h2>
    <div class="partner-row">
      <span class="partner"><i></i>Linkspan</span>
      <span class="partner">Aurelon Radio</span>
      <span class="partner">Meridex</span>
      <span class="partner">Kestrel Air</span>
      <span class="partner">Northwire</span>
      <span class="partner">Tallpine</span>
    </div>
  </section>

  <footer class="footer">
    <div class="footer-links">Privacy Policy | Terms Conditions | Sitemap | Contact Us</div>
    <div class="copyright">Copyright © 2014 &nbsp;All Rights Reserved</div>
    <div class="follow">FOLLOW US</div>
    <div class="social" aria-label="Social links">
      <i style="background:#f39a1e"></i><i style="background:#2aa3dd"></i><i style="background:#3b5a98"></i><i style="background:#2d7fd1"></i><i style="background:#2a86b8"></i><i style="background:#d8262a"></i>
    </div>
  </footer>
</div>
</body>
</html>
```